Upmarket Dessert Lounge needs a Business Card Design

We are an upmarket dessert lounge needing a business card to match our image.

We want something that is simple yet beautiful, feminine, classy, sophisticated and elegant. We want it to stand out and don't mind if it is bold.

The design should include our logo and colours of red or maroon with gold highlights. We don't mind if black is used.

Marlow & Quince

Target Market(s)

For those who like to indulge or treat themselves and give in to their temptations on good quality desserts.

Industry/Entity Type

Business

Requirements
Must have
• Must include our logo and our name

Marlow & Quince

M & Q

```html
<!DOCTYPE html>
<html lang="en">
<head>
<meta charset="utf-8">
<title>Marlow &amp; Quince — Business Card</title>
<link rel="stylesheet" href="https://fonts.googleapis.com/css2?family=Cinzel:wght@400;600&family=Lora:wght@400&family=Open+Sans:wght@400&display=swap">
<style>
  :root {
    --page-bg: #efe6e6;
    --card-red: #9c2a25;
    --gold: #f0b978;
    --gold-soft: #d9a46a;
    --cream: #fbeee0;
    --white: #ffffff;
  }
  html, body {
    margin: 0;
    padding: 0;
    width: 1200px;
    height: 951px;
    overflow: hidden;
    background: var(--page-bg);
  }
  .canvas {
    position: relative;
    width: 1200px;
    height: 951px;
  }
  .card {
    position: absolute;
    width: 640px;
    height: 366px;
    border-radius: 24px;
    background: var(--card-red);
    box-shadow: 0 10px 24px rgba(80, 30, 30, 0.25);
    overflow: hidden;
  }
  .card--front { left: 80px; top: 80px; }
  .card--back { left: 480px; top: 505px; }

  .corner-flourish {
    position: absolute;
    right: 0;
    top: 0;
    width: 340px;
    height: 170px;
    background: radial-gradient(ellipse 170px 95px at 62% 22%,
      rgba(240, 185, 120, 0.5) 0%,
      rgba(240, 185, 120, 0.22) 50%,
      rgba(240, 185, 120, 0) 100%);
  }

  .wordmark {
    position: absolute;
    font-family: "Cinzel", serif;
    font-weight: 400;
    color: var(--cream);
    letter-spacing: 0.04em;
    white-space: nowrap;
    margin: 0;
  }
  .wordmark--front {
    left: 0;
    right: 0;
    top: 148px;
    text-align: center;
    font-size: 40px;
  }
  .web-address {
    position: absolute;
    left: 0;
    right: 0;
    bottom: 46px;
    text-align: center;
    font-family: "Lora", serif;
    font-size: 18px;
    letter-spacing: 0.06em;
    color: var(--gold);
    margin: 0;
  }

  .wordmark--back {
    left: 30px;
    top: 140px;
    width: 270px;
    text-align: center;
    font-size: 58px;
    line-height: 1;
    font-weight: 600;
  }
  .contact {
    position: absolute;
    right: 48px;
    top: 110px;
    text-align: right;
    font-family: "Open Sans", sans-serif;
    color: var(--white);
    font-size: 17px;
    line-height: 1.3;
  }
  .contact__name {
    margin: 0 0 16px;
    font-size: 24px;
    color: var(--gold);
  }
  .contact__address { margin: 0 0 14px; }
  .contact__lines { margin: 0; }
  .edge-bar {
    position: absolute;
    right: 0;
    top: 208px;
    width: 14px;
    height: 64px;
    background: var(--gold-soft);
  }
</style>
</head>
<body>
<main class="canvas">
  <section class="card card--front" aria-label="Card front">
    <div class="corner-flourish" role="img" aria-label="Gold floral flourish in the top corner"></div>
    <p class="wordmark wordmark--front">MARLOW &amp; QUINCE</p>
    <p class="web-address">www.marlowquince.com</p>
  </section>

  <section class="card card--back" aria-label="Card back">
    <p class="wordmark wordmark--back">M &amp; Q</p>
    <div class="contact">
      <p class="contact__name">Marlow &amp; Quince</p>
      <p class="contact__address">48 Harbor Lane, Suite 300<br>Portland, Maine 04101</p>
      <p class="contact__lines">207-555-0142<br>info@marlowquince.com</p>
    </div>
    <div class="edge-bar"></div>
  </section>
</main>
</body>
</html>
```